Browser extension - redesign of extension and website

We need style improvement of our website for extension Dusk Lens (https://dusklens.example) and (https://store.example/detail/dark-mode-dusk-lens/qwpzrtyvbnmkhgfdsaxcvplokijuhyt) that incorporated dark mode in it heart. The main purpose of the extension is transforming webpages to "dark mode" and to apply many other filters for more pleasant viewing in dark environment. The final design should communicate safety, professional and love of dark mode.
What we need:
- Improved color schema - that is modern and reflect the purpose of the app (it will be used for both the website and the extension)
- Improved Logo based on current logo
- Style guide - for website and extension
- Good UI/UX for the flows of website - based on the purpose to download the extension. The user should be guided to see what the extension do and after that to download the extension
- Webpages that we need design for:
- Home page (https://dusklens.example),
- How to Start Page (https://dusklens.example/how-to-start/),
- Client Area (https://billing.dusklens.example/client/login),
- FAQ (https://dusklens.example/help/) ,
- Browser Template 1 (https://dusklens.example/chrome-dark-mode/)
- Browser Template 2 (https://dusklens.example/firefox-dark-mode/)
-Activation Instructions - https://dusklens.example/activation-instructions/

We are attaching our logo for reference and screenshots of our current website.

Please start with home page design first and extension home page, after submitting that we will evaluate and proceed accordingly.

Target Market(s)

Everyone who likes dark mode from 18+ till 65+ so we can make easy for them to read at dark places.

Industry/Entity Type

Software

Number of Pages Required

5+ page

Font styles to use
Sans Serif

Requirements
Must have
• Dark color scheme, To inspire confidence in an extension,
Should not have
• Do not use pure black as background.

```html
<!DOCTYPE html>
<html lang="en">
<head>
<meta charset="utf-8">
<title>Dusk Lens – Dark mode on any website</title>
<link href="https://fonts.googleapis.com/css2?family=Poppins:wght@300;400;500;600;700&family=Montserrat:wght@400;500;600;700&display=swap" rel="stylesheet">
<style>
:root{
  --canvas:#e3e5e6;
  --ink:#04090c;
  --deep:#061419;
  --band:#083b42;
  --benefit:#06252b;
  --teal:#0d5e66;
  --accent:#1fa7b3;
  --accent-soft:#58c6cf;
  --text:#ffffff;
  --muted:#c9d5d8;
}
*{margin:0;padding:0;box-sizing:border-box}
html,body{width:1200px;height:4000px;overflow:hidden}
body{background:var(--canvas);font-family:"Montserrat",sans-serif;color:var(--text)}
.page{position:absolute;left:100px;top:0;width:1000px;height:4000px;background:var(--ink);overflow:hidden}
section,header,footer{position:relative;width:1000px}
.brand{display:flex;align-items:center;gap:12px;font-family:"Poppins",sans-serif;font-weight:600;color:var(--accent);letter-spacing:1px}
.brand-dot{border-radius:50%;border:3px solid var(--accent);display:inline-block}
/* nav */
.site-nav{height:77px;background:var(--ink);display:flex;align-items:center;justify-content:space-between;padding:0 30px 0 22px}
.site-nav .brand{font-size:31px}
.site-nav .brand-dot{width:26px;height:26px}
.nav-links{display:flex;gap:58px;list-style:none;font-family:"Poppins",sans-serif;font-size:17px;color:var(--accent)}
/* hero */
.hero{height:572px;background:var(--ink)}
.hero-photo{position:absolute;inset:0;background:radial-gradient(ellipse at 30% 40%,#5a4428 0%,#2a2218 30%,transparent 60%),radial-gradient(ellipse at 80% 35%,#17454c 0%,#0a2227 40%,transparent 70%),linear-gradient(180deg,#1a1a16 0%,#0d1212 70%,#050809 100%)}
.hero-curve{position:absolute;left:0;top:0}
.hero-copy{position:absolute;top:148px;left:0;width:1000px;text-align:center}
.hero-title{font-family:"Poppins",sans-serif;font-weight:400;font-size:38px;line-height:50px;letter-spacing:.5px}
.hero-title mark{background:#fff;color:#000;font-weight:600;padding:0 4px}
.hero-sub{font-family:"Poppins",sans-serif;font-weight:600;font-size:17px;margin-top:8px}
.btn{display:inline-block;background:var(--accent);color:#fff;font-family:"Poppins",sans-serif;font-weight:600;font-size:18px;padding:3px 18px;margin-top:24px}
/* section headings */
.sec-title{font-family:"Poppins",sans-serif;font-weight:600;font-size:34px;letter-spacing:2px;text-align:center}
.sec-title span{border-bottom:3px solid var(--accent);padding-bottom:2px}
.sec-lead{font-size:15px;line-height:18px;text-align:center;color:var(--muted);width:700px;margin:14px auto 0}
/* features */
.features{height:560px;background:var(--ink);padding-top:68px}
.feature-grid{position:absolute;top:182px;left:23px;display:flex;gap:12px}
.feature-card{width:228px;height:282px;border:2px solid #d8dfe1;border-radius:8px;text-align:center;padding:14px 12px}
.feature-card.is-active{background:var(--teal);border-color:var(--teal)}
.feature-icon{width:74px;height:74px;border-radius:50%;background:#fff;margin:0 auto;display:flex;align-items:center;justify-content:center}
.feature-card:not(.is-active) .feature-icon{background:#0d4f57}
.feature-card h3{font-family:"Poppins",sans-serif;font-weight:500;font-size:14px;letter-spacing:.6px;margin-top:18px}
.feature-card p{font-size:10.5px;line-height:12.5px;margin-top:14px;color:var(--muted)}
/* video band */
.release{height:370px;background:var(--band)}
.video{position:absolute;left:33px;top:29px;width:563px;height:313px;background:radial-gradient(ellipse at 50% 52%,#ffffff 0%,#c88cff 6%,#5a2ad0 18%,#1a1450 36%,#0a0a1a 60%)}
.video-bar{position:absolute;left:12px;top:10px;font-size:12px;display:flex;gap:8px;align-items:center}
.video-bar i{width:24px;height:24px;border-radius:50%;background:var(--band);display:inline-block}
.video-play{position:absolute;left:258px;top:136px;width:46px;height:32px;border-radius:8px;background:#e02020}
.video-play::after{content:"";position:absolute;left:18px;top:9px;border-left:12px solid #fff;border-top:7px solid transparent;border-bottom:7px solid transparent}
.video-watch{position:absolute;left:10px;bottom:12px;font-size:11px;font-weight:600}
.release-notes{position:absolute;left:655px;top:46px;width:320px}
.release-notes h2{font-family:"Poppins",sans-serif;font-weight:500;font-size:22px;letter-spacing:1.5px}
.release-notes ul{list-style:none;margin-top:22px}
.release-notes li{font-size:14px;line-height:17px;margin-bottom:9px;padding-left:22px;position:relative}
.release-notes li::before{content:"";position:absolute;left:0;top:2px;width:12px;height:12px;border:2px solid #fff;border-radius:50%;box-shadow:inset 0 0 0 2px var(--band),inset 0 0 0 6px #fff}
/* partners */
.partners{height:160px;background:var(--ink);display:flex;align-items:center;justify-content:space-around;padding:0 20px}
.partner{display:flex;align-items:center;gap:8px;font-family:"Poppins",sans-serif;font-weight:500;font-size:22px;color:#d8e2e4}
.partner i{width:16px;height:16px;border-radius:50%;background:var(--accent);display:inline-block}
/* benefits */
.benefits{height:608px;background:var(--benefit);padding-top:48px}
.benefit-grid{display:grid;grid-template-columns:repeat(3,326px);row-gap:48px;justify-content:center;margin-top:66px}
.benefit{text-align:center}
.benefit svg{display:block;margin:0 auto}
.benefit h3{font-family:"Poppins",sans-serif;font-weight:500;font-size:23px;margin-top:6px}
.benefit p{font-size:11px;line-height:14px;width:220px;margin:4px auto 0;color:var(--muted)}
/* plans */
.plans{height:547px;background:var(--deep);padding-top:56px}
.plans .sec-lead{width:860px}
.plans .sec-lead b{color:#fff}
.plan-grid{position:absolute;top:177px;left:23px;display:flex;gap:12px}
.plan{width:232px;height:288px;border:2px solid #d8dfe1;border-radius:8px;text-align:center;padding-top:18px}
.plan.is-free{border-color:transparent}
.plan-price{font-family:"Poppins",sans-serif;font-weight:700;font-size:30px}
.plan-price small{font-weight:400;font-size:26px}
.plan li{list-style:none;font-size:13px;line-height:32px}
.plan ul{margin-top:6px}
.plan-select{font-family:"Poppins",sans-serif;font-weight:700;font-size:28px;letter-spacing:1px;margin-top:4px}
/* news */
.news{height:551px;background:#041419;padding-top:56px}
.story-main{position:absolute;left:113px;top:182px;width:330px;height:300px;background:#071c22}
.story-main .shot{height:196px;background:linear-gradient(90deg,#f2f2f2 0%,#f2f2f2 55%,#2c2c2c 55%,#3a3a3a 100%)}
.story-date{font-size:12px;font-family:"Poppins",sans-serif}
.story-main .story-date{margin:14px 0 0 14px}
.story-main h3{font-family:"Poppins",sans-serif;font-weight:500;font-size:22px;letter-spacing:1.5px;margin-left:14px}
.read-more{position:absolute;right:10px;bottom:8px;font-size:11px;color:var(--accent);letter-spacing:.8px}
.story{position:absolute;left:503px;width:334px;height:150px;background:#071c22;display:flex}
.story .shot{width:179px;height:140px;margin-top:-4px}
.story .body{padding:10px 0 0 10px;position:relative;flex:1}
.story h3{font-family:"Poppins",sans-serif;font-weight:600;font-size:13.5px;line-height:16px;margin-top:6px}
/* browsers */
.browsers{height:217px;background:var(--ink);padding-top:60px}
.browsers .sec-title{font-weight:400;font-size:32px;letter-spacing:3px}
.browser-row{display:flex;justify-content:center;gap:26px;margin-top:34px}
.browser{display:flex;flex-direction:column;align-items:center;gap:4px;font-size:12px;width:84px}
.browser i{width:38px;height:38px;border-radius:50%;background:var(--accent);display:block}
/* footer */
.site-footer{height:338px;background:var(--teal)}
.footer-bg{position:absolute;left:0;top:0}
.site-footer .brand{position:absolute;left:0;width:1000px;justify-content:center;top:78px;font-size:58px;font-weight:500}
.site-footer .brand-dot{width:52px;height:52px;border-width:5px}
.footer-links{position:absolute;top:200px;left:0;width:1000px;display:flex;justify-content:center;gap:56px;list-style:none;font-family:"Poppins",sans-serif;font-size:17px}
.footer-rule{position:absolute;top:248px;left:0;width:1000px;border-top:1px solid #2d7880}
.social{position:absolute;top:284px;left:0;width:1000px;display:flex;justify-content:center;gap:58px;list-style:none;font-family:"Poppins",sans-serif;font-weight:600;font-size:16px}
</style>
</head>
<body>
<div class="page">

<header class="site-nav">
  <div class="brand"><i class="brand-dot"></i>DUSK LENS</div>
  <ul class="nav-links"><li>Home</li><li>How to start</li><li>Client</li><li>FAQ</li></ul>
</header>

<section class="hero">
  <div class="hero-photo" role="img" aria-label="Photo of people working at computers in a dim room lit by teal screens"></div>
  <svg class="hero-curve" width="1000" height="572" viewBox="0 0 1000 572">
    <path d="M0 500 Q500 640 1000 500 L1000 572 L0 572 Z" fill="#04090c"/>
    <path d="M0 428 Q500 650 1000 428" fill="none" stroke="#1fa7b3" stroke-width="4"/>
    <path d="M0 448 Q500 610 1000 448" fill="none" stroke="#0d5e66" stroke-width="6"/>
  </svg>
  <div class="hero-copy">
    <h1 class="hero-title">PROTECT YOUR EYES, ENABLE <mark>DARK</mark><br><mark>MODE</mark> ON ANY WEBSITE!</h1>
    <p class="hero-sub">Smart conversion, no ads, no data mining, helpful support!</p>
    <span class="btn">DOWNLOAD NOW</span>
  </div>
</section>

<section class="features">
  <h2 class="sec-title">OUR <span>FEATURES</span></h2>
  <p class="sec-lead">Lorem Ipsum is simply dummy text of the printing and typesetting industry. Lorem Ipsum has been the industry's standard dummy text ever since the 1500s</p>
  <div class="feature-grid">
    <article class="feature-card is-active">
      <div class="feature-icon"><svg width="38" height="38" viewBox="0 0 24 24" fill="none" stroke="#0d5e66" stroke-width="1.8"><path d="M4 20l4-1 11-11-3-3L5 16z"/><path d="M14 7l3 3"/></svg></div>
      <h3>SMART CONVERSION</h3>
      <p>Instead of inverting, we are converting the colors. Unlike its competitors, Dusk Lens takes a unique approach to each webpage. It analyses the page colors and converts them in a way to provide you with smooth and consistent dark mode. No simple color inversions, no bright spots and flashes.</p>
    </article>
    <article class="feature-card">
      <div class="feature-icon"><svg width="40" height="40" viewBox="0 0 24 24" fill="none" stroke="#fff" stroke-width="1.6"><path d="M2 12s4-6 10-6 10 6 10 6-4 6-10 6S2 12 2 12z"/><circle cx="12" cy="12" r="3"/></svg></div>
      <h3>PROTECT YOUR EYES</h3>
      <p>Staring at your screen for 10-12 hours a day is surely taking toll on your eyes. Having dark mode that is consistent on all websites is the best way to reduce the eye strain, headache and watery eyes.</p>
    </article>
    <article class="feature-card">
      <div class="feature-icon"><svg width="40" height="40" viewBox="0 0 24 24" fill="none" stroke="#fff" stroke-width="1.6"><circle cx="12" cy="9" r="4"/><path d="M5 21c0-4 3-6 7-6s7 2 7 6"/><path d="M7 9a5 5 0 0110 0"/></svg></div>
      <h3>HELPFUL SUPPORT</h3>
      <p>Helpful support, ready to answer your questions. We built an internal chat system that you can use to reach out to us directly from the extension. Encountered a broken website, we are here to fix it for you.</p>
    </article>
    <article class="feature-card">
      <div class="feature-icon"><svg width="40" height="40" viewBox="0 0 24 24" fill="none" stroke="#fff" stroke-width="1.6"><circle cx="12" cy="12" r="8"/><path d="M6 18L18 6"/></svg></div>
      <h3>NO ADS &amp; DATA MINING</h3>
      <p>Dusk Lens does not monitor, process nor store your browsing activity. No ads even on the Lite (free version).</p>
    </article>
  </div>
</section>

<section class="release">
  <div class="video" role="img" aria-label="Video cover showing a glowing stylised eye on a dark background">
    <div class="video-bar"><i></i>Dark Mode - Dusk Lens Extension - on any website</div>
    <div class="video-play"></div>
    <div class="video-watch">Watch on Vidora</div>
  </div>
  <div class="release-notes">
    <h2>LATEST VERSION</h2>
    <ul>
      <li>Tasktrack dark mode - custom theme</li>
      <li>Wikiflow dark mode - custom theme</li>
      <li>CodeBucket dark mode - custom theme</li>
      <li>NORMAL mode - mutator - to add missing attribute</li>
      <li>Shopnest.example - product image dark mode</li>
      <li>Change order of injected custom code</li>
    </ul>
  </div>
</section>

<section class="partners">
  <span class="partner"><i></i>Taskfield</span>
  <span class="partner"><i></i>Redwing</span>
  <span class="partner"><i></i>Corelane</span>
  <span class="partner"><i></i>Metrica</span>
  <span class="partner"><i></i>Chatterbox</span>
  <span class="partner"><i></i>Ovalbase</span>
</section>

<section class="benefits">
  <h2 class="sec-title">BENEFITS OF <span>DARK</span> WEB</h2>
  <p class="sec-lead" style="width:800px">Dusk Lens extension is a great tool to protect your eyes if you are browsing late at night, working in in low-light environment or read extensively.</p>
  <div class="benefit-grid">
    <div class="benefit"><svg width="42" height="42" viewBox="0 0 24 24"><circle cx="12" cy="12" r="9" fill="none" stroke="#fff" stroke-width="2"/><path d="M12 3a9 9 0 010 18z" fill="#fff"/></svg><h3>Color changer</h3><p>Reinvent your browsing experience by changing any color on any website. You can customise a single website or all with couple of clicks.</p></div>
    <div class="benefit"><svg width="42" height="42" viewBox="0 0 24 24" fill="none" stroke="#fff" stroke-width="1.6"><circle cx="12" cy="12" r="4"/><path d="M12 2v3M12 19v3M2 12h3M19 12h3M5 5l2 2M17 17l2 2M5 19l2-2M17 7l2-2"/></svg><h3>Brightness</h3><p>Adjust the brightness, the contrast and the saturation to match the recommended healthy levels and protect your eyes.</p></div>
    <div class="benefit"><svg width="42" height="42" viewBox="0 0 24 24" fill="none" stroke="#fff" stroke-width="1.4"><path d="M3 7c3-2 3 2 6 0s3 2 6 0 3 2 6 0M3 12c3-2 3 2 6 0s3 2 6 0 3 2 6 0M3 17c3-2 3 2 6 0s3 2 6 0 3 2 6 0"/></svg><h3>Dimming</h3><p>Extremely useful if you are working in dark space/room and the screen is the only source of light in the room.</p></div>
    <div class="benefit"><svg width="42" height="42" viewBox="0 0 24 24" fill="none" stroke="#fff" stroke-width="1.5"><rect x="3" y="7" width="18" height="13" rx="2"/><path d="M8 7l2-3h4l2 3"/><circle cx="12" cy="13" r="3.5"/></svg><h3>Image Conversion</h3><p>We analyse and convert only the small images and icons in a website to give you even smoother experience. Social feed posts and other significant media is not converted.</p></div>
    <div class="benefit"><svg width="42" height="42" viewBox="0 0 24 24" fill="none" stroke="#fff" stroke-width="2"><circle cx="12" cy="12" r="5"/><circle cx="12" cy="12" r="9" stroke-dasharray="3 2.6"/></svg><h3>Blue Light Filter</h3><p>Take care of your eyes by eliminating the blue light coming from your screen. Highly recommended especially during late night browsing.</p></div>
    <div class="benefit"><svg width="42" height="42" viewBox="0 0 24 24" fill="none" stroke="#fff" stroke-width="1.5"><circle cx="12" cy="8" r="4"/><path d="M4 21c0-5 4-7 8-7s8 2 8 7z"/></svg><h3>Real Support</h3><p>We DO provide support to everyone who installed the extension. Simply use our messaging center by opening the extension.</p></div>
  </div>
</section>

<section class="plans">
  <h2 class="sec-title"><span>PLANS</span></h2>
  <p class="sec-lead">Install now and get <b>3 months</b> of Dusk Lens Pro for <b>free!</b><br>Afterwards the price is a little over 2 cents per day or you can choose the <b>free version - Dusk Lens Lite</b></p>
  <div class="plan-grid">
    <div class="plan is-free"><div class="plan-price">FREE</div><ul><li>Upto 1 Browser</li><li>5 Websites</li><li>Any Website</li><li>Available on All Browser</li><li>Help 24/7</li></ul><div class="plan-select">SELECT</div></div>
    <div class="plan"><div class="plan-price">$9 / <small>Yearly</small></div><ul><li>Upto 3 Browser</li><li>Unlimited Websites</li><li>Any Website</li><li>Available on All Browser</li><li>Help 24/7</li></ul><div class="plan-select">SELECT</div></div>
    <div class="plan"><div class="plan-price">$14 / <small>Yearly</small></div><ul><li>Upto 6 Browser</li><li>Unlimited Websites</li><li>Any Website</li><li>Available on All Browser</li><li>Help 24/7</li></ul><div class="plan-select">SELECT</div></div>
    <div class="plan"><div class="plan-price">$40 / <small>One-time</small></div><ul><li>Upto 10 Browser</li><li>Unlimited Websites</li><li>Any Website</li><li>Available on All Browser</li><li>Help 24/7</li></ul><div class="plan-select">SELECT</div></div>
  </div>
</section>

<section class="news">
  <h2 class="sec-title" style="font-weight:500">DUSK LENS <span>IN</span> THE NEWS</h2>
  <p class="sec-lead">Lorem Ipsum is simply dummy text of the printing and typesetting industry. Lorem Ipsum has been the industry's standard dummy text ever since the 1500s</p>
  <article class="story-main">
    <div class="shot" role="img" aria-label="Screenshot of a blog feed shown in light and dark mode side by side"></div>
    <p class="story-date">25-NOV-2022</p>
    <h3>NOW ON TUMBLEWIRE</h3>
    <span class="read-more">READ MORE</span>
  </article>
  <article class="story" style="top:182px">
    <div class="shot" role="img" aria-label="Photo of a person reading a phone in bed at night" style="background:linear-gradient(135deg,#1d3a5c,#4a7fb0 50%,#0e1e30)"></div>
    <div class="body"><p class="story-date">25-NOV-2022</p><h3>BCN - READ THE<br>NEWS IN DARK<br>MODE</h3><span class="read-more">READ MORE</span></div>
  </article>
  <article class="story" style="top:351px">
    <div class="shot" role="img" aria-label="Photo of a desk with a laptop lit in pink and purple light" style="background:linear-gradient(135deg,#2a1030,#c0307a 45%,#3a2a80 75%,#101020)"></div>
    <div class="body"><p class="story-date">25-NOV-2022</p><h3>BCN - READ THE<br>NEWS IN DARK<br>MODE</h3><span class="read-more">READ MORE</span></div>
  </article>
</section>

<section class="browsers">
  <h2 class="sec-title">AVAILABLE <span>IN</span> EVERY <b>BROWSER</b></h2>
  <div class="browser-row">
    <span class="browser"><i></i>Orbis</span>
    <span class="browser"><i></i>Emberfox</span>
    <span class="browser"><i></i>Tidewave</span>
    <span class="browser"><i></i>Compass</span>
    <span class="browser"><i></i>Arion</span>
    <span class="browser"><i></i>Yarrow</span>
    <span class="browser"><i></i>Kitsu</span>
    <span class="browser"><i></i>Violet</span>
    <span class="browser"><i></i>Bastion</span>
  </div>
</section>

<footer class="site-footer">
  <svg class="footer-bg" width="1000" height="338" viewBox="0 0 1000 338">
    <rect width="1000" height="338" fill="#04090c"/>
    <path d="M0 120 Q500 -60 1000 120 L1000 338 L0 338 Z" fill="#0a3f46"/>
    <path d="M0 110 Q500 -70 1000 110" fill="none" stroke="#1fa7b3" stroke-width="4"/>
    <path d="M0 128 Q500 -40 1000 128" fill="none" stroke="#0d5e66" stroke-width="6"/>
  </svg>
  <div class="brand"><i class="brand-dot"></i>DUSK LENS</div>
  <ul class="footer-links"><li>Home</li><li>How to start</li><li>Install Now</li><li>Merchandise</li><li>FAQ</li></ul>
  <div class="footer-rule"></div>
  <ul class="social"><li>Chirpy</li><li>Linkly</li><li>Vidora</li><li>Social</li><li>Snapgram</li></ul>
</footer>

</div>
</body>
</html>
```